Construction material supplies company business card ****

1. Full company name “K T Masonry Works Ltd”
I am after a Business card design for the company as a whole. We are better known in Solomon Islands as “K T Masonry” for short.

We are a building materials supplier of
Ready Mixed Concrete, Bricks and Blocks,
Quarry products- gravel, aggregates, sand etc.
Cement distributor/retailer of reputable brands.
Other prefab concrete products. Culverts, wave breakers, concrete retaining blocks etc.

2. Competitive Advantage over Competition: Quality, efficient, professional, dependable, reliable

3. We want people to feel trust worthy, high quality, strong when they see our brand

5. No preference to color. Maybe more sturdy and corporate. Not fancy.

Industry/Entity Type

CONSTRUCTION SUPPLY

Contact Information for Business Card

Name, Position, office phone mob phone, email

Requirements
Must have
• the company logo
Nice to have
• would like to see a mixture of designs, of with logo only and also with simple graphic designs to bring out the company whilst still have the strong sturdy professional feeling

```html
<!DOCTYPE html>
<html lang="en">
<head>
<meta charset="utf-8">
<title>K T Masonry – Business Card</title>
<link href="https://fonts.googleapis.com/css2?family=Roboto:wght@400;500;700&display=swap" rel="stylesheet">
<style>
  :root {
    --page-bg: #2a2a2a;
    --navy: #1d3f63;
    --navy-mid: #34587e;
    --navy-light: #4a6d92;
    --navy-band: rgba(16, 40, 70, 0.72);
    --paper: #e4e6e8;
    --paper-light: #eef0f1;
    --white: #f3f4f5;
    --text-soft: #e3e9ef;
  }
  * { box-sizing: border-box; margin: 0; padding: 0; }
  html, body { width: 1200px; height: 1138px; overflow: hidden; }
  body {
    background: var(--page-bg);
    font-family: "Roboto", Arial, sans-serif;
    position: relative;
  }
  .card {
    position: absolute;
    left: 290px;
    width: 620px;
    height: 375px;
    border-radius: 16px;
    overflow: hidden;
    box-shadow: 0 8px 18px rgba(0,0,0,0.45);
  }
  /* Front */
  .card-front {
    top: 186px;
    background: linear-gradient(160deg, var(--navy-light) 0%, var(--navy-mid) 45%, #2c4d72 100%);
    color: var(--white);
    text-align: center;
  }
  .brand-name {
    font-family: "Roboto", Arial, sans-serif;
    font-weight: 700;
    letter-spacing: 2px;
    text-transform: uppercase;
    white-space: nowrap;
  }
  .card-front .brand-name {
    position: absolute;
    top: 70px; left: 0; right: 0;
    font-size: 54px;
    line-height: 60px;
    color: var(--white);
  }
  .intro-pill {
    position: absolute;
    top: 185px;
    left: 137px;
    width: 346px;
    height: 40px;
    border-radius: 20px;
    background: rgba(30, 62, 98, 0.85);
    box-shadow: 0 0 0 2px rgba(255,255,255,0.08);
    font-size: 16px;
    line-height: 40px;
    z-index: 2;
  }
  .product-band {
    position: absolute;
    top: 215px; left: 0; right: 0;
    height: 78px;
    background: var(--navy-band);
    padding-top: 28px;
    font-size: 16px;
    line-height: 22px;
    color: var(--text-soft);
  }
  .product-extra {
    position: absolute;
    top: 306px; left: 0; right: 0;
    font-size: 16px;
    line-height: 24px;
    color: var(--text-soft);
  }
  /* Back */
  .card-back {
    top: 608px;
    background: linear-gradient(135deg, var(--paper-light) 0%, var(--paper) 60%, #d9dcdf 100%);
    color: var(--navy);
  }
  .card-back .brand-name {
    position: absolute;
    top: 60px; left: 36px;
    font-size: 50px;
    line-height: 60px;
    color: var(--navy);
  }
  .person { position: absolute; top: 192px; left: 36px; }
  .person-name { font-size: 22px; font-weight: 700; line-height: 28px; }
  .person-role { font-size: 16px; line-height: 22px; }
  .address {
    position: absolute; top: 282px; left: 36px;
    font-size: 16px; line-height: 26px;
  }
  .contact-list {
    position: absolute; top: 204px; left: 336px;
    list-style: none;
    font-size: 16px;
  }
  .contact-list li {
    display: flex; align-items: center;
    height: 26px;
  }
  .contact-list svg { width: 14px; height: 14px; margin-right: 18px; fill: var(--navy); }
  .tagline-band {
    position: absolute; right: 0; bottom: 0;
    width: 385px; height: 47px;
  }
  .tagline-band svg { position: absolute; inset: 0; }
  .tagline-band p {
    position: absolute; right: 20px; top: 0;
    line-height: 47px;
    font-size: 16px;
    color: var(--white);
  }
</style>
</head>
<body>

<section class="card card-front" aria-label="Business card front">
  <div class="brand-name">K T Masonry</div>
  <div class="intro-pill">We are a building materials supplier of</div>
  <div class="product-band">
    <p>Ready Mixed Concrete, Bricks and Blocks, Quarry Products</p>
    <p>Quarry Products:- Gravel, Aggregates, Sand Etc.</p>
  </div>
  <div class="product-extra">
    <p>Cement Distributor/Retailer of Reputable Brands.</p>
    <p>Other Concrete Products Culverts, Wave Breakers, Concrete Retaining Blocks</p>
  </div>
</section>

<section class="card card-back" aria-label="Business card back">
  <div class="brand-name">K T Masonry</div>

  <div class="person">
    <p class="person-name">Daniel Reeves</p>
    <p class="person-role">Managing Director</p>
  </div>

  <p class="address">41 Quarry Lane, Port City,<br>Any Town, US 654321</p>

  <ul class="contact-list">
    <li>
      <svg viewBox="0 0 16 16" aria-hidden="true"><path d="M1 5c0-2 3-3 7-3s7 1 7 3v1h-4V4.5H5V6H1zM4 7h8l2 7H2z"/></svg>
      000 0000 0000
    </li>
    <li>
      <svg viewBox="0 0 16 16" aria-hidden="true"><path d="M1 3h14v10H1zm1.5 1.2v.3L8 9l5.5-4.5v-.3zM2.5 6.4v5.1l3.4-2.4zm11 0-3.4 2.7 3.4 2.4z"/></svg>
      daniel@ktmasonry.com
    </li>
    <li>
      <svg viewBox="0 0 16 16" aria-hidden="true"><path d="M8 1a7 7 0 1 0 0 14A7 7 0 0 0 8 1zm-1 1.7V5H4.3A5.6 5.6 0 0 1 7 2.7zm2 0A5.6 5.6 0 0 1 11.7 5H9zM3.6 6.5H7v3H3.6a5.6 5.6 0 0 1 0-3zm5.4 0h3.4a5.6 5.6 0 0 1 0 3H9zM4.3 11H7v2.3A5.6 5.6 0 0 1 4.3 11zM9 11h2.7A5.6 5.6 0 0 1 9 13.3z"/></svg>
      www.ktmasonry.com
    </li>
  </ul>

  <div class="tagline-band">
    <svg viewBox="0 0 385 47" preserveAspectRatio="none" aria-hidden="true">
      <polygon points="22,0 385,0 385,47 0,47" fill="#1d3f63"/>
    </svg>
    <p>Efficient, Professional, Dependable, Reliable</p>
  </div>
</section>

</body>
</html>
```